Brindle Yard Care. The best in the biz

I run a lawn care service that offers full service mowing. 100% satisfaction guarantee. Fast, Friendly, quality service "I am your lawns best friend" I cut residential lawns. I offer a mow package that includes trimming, edging and clean up. Prices very from 20 dollars to 75. I want my logo to stand out. Free estimates

Target Market(s)

Home owners

Industry/Entity Type

Landscaping

Contact Information for Business Card

555-812-4473 tomvale48@quillmail.net Derek. Brindle Yard care

Colors
f37122
9bcb3c
cadf82

Requirements
Must have
• Company name.
• Phone number
• Email
• My services
• images
Nice to have
• A sun that is growing grass.
Should not have
• Incorrect information

```html
<!DOCTYPE html>
<html lang="en">
<head>
<meta charset="utf-8">
<title>Brindle Yard Care — Business Card</title>
<link rel="stylesheet" href="https://fonts.googleapis.com/css2?family=Open+Sans:wght@400;600;700&family=Roboto:wght@400&display=swap">
<style>
  :root {
    --orange: #f37122;
    --green: #9bcb3c;
    --green-text: #8cc63f;
    --green-pale: #cadf82;
    --slate: #5f5f5f;
    --paper: #ffffff;
    --backdrop: #e9e7e4;
  }
  * { margin: 0; padding: 0; box-sizing: border-box; }
  html, body {
    width: 1200px; height: 900px; overflow: hidden;
    background: var(--backdrop);
  }
  .stage { position: relative; width: 1200px; height: 900px; }

  .card {
    position: absolute;
    width: 556px; height: 343px;
    overflow: hidden;
    box-shadow: 0 6px 18px rgba(0,0,0,0.12);
  }

  /* Front */
  .card--front { left: 238px; top: 62px; background: var(--paper); }
  .brand-dot {
    position: absolute; left: 110px; top: 64px;
    width: 76px; height: 76px; border-radius: 50%;
    background: var(--slate);
  }
  .brand-name {
    position: absolute; left: 26px; top: 144px;
    font-family: "Roboto", sans-serif; font-weight: 400;
    font-size: 28px; color: var(--green-text); white-space: nowrap;
  }
  .contact { position: absolute; left: 277px; top: 204px; font-family: "Open Sans", sans-serif; }
  .contact__name { font-weight: 600; font-size: 18px; color: var(--green-text); margin-bottom: 21px; }
  .contact__line {
    display: flex; align-items: center; gap: 8px;
    font-size: 15px; color: var(--orange); line-height: 21px;
  }
  .contact__line svg { width: 11px; height: 11px; fill: var(--green-text); flex: none; }

  /* Back */
  .card--back { left: 457px; top: 518px; width: 560px; background: var(--orange); }
  .back-disc {
    position: absolute; left: -178px; top: -6px;
    width: 356px; height: 356px; border-radius: 50%;
    background: var(--slate);
  }
  .promises {
    position: absolute; left: 222px; top: 104px;
    list-style: none;
    font-family: "Open Sans", sans-serif; font-weight: 700;
    font-size: 18px; color: var(--paper);
  }
  .promises li { height: 52px; line-height: 28px; }
</style>
</head>
<body>
<main class="stage">
  <section class="card card--front" aria-label="Business card front">
    <span class="brand-dot" aria-hidden="true"></span>
    <h1 class="brand-name">Brindle Yard Care</h1>
    <div class="contact">
      <p class="contact__name">Derek</p>
      <p class="contact__line">
        <svg viewBox="0 0 24 24" aria-hidden="true"><path d="M6.6 10.8a15 15 0 0 0 6.6 6.6l2.2-2.2a1 1 0 0 1 1-.25 11.4 11.4 0 0 0 3.6.57 1 1 0 0 1 1 1V20a1 1 0 0 1-1 1A17 17 0 0 1 3 4a1 1 0 0 1 1-1h3.5a1 1 0 0 1 1 1c0 1.25.2 2.45.57 3.57a1 1 0 0 1-.25 1z"/></svg>
        555-812-4473
      </p>
      <p class="contact__line">
        <svg viewBox="0 0 24 24" aria-hidden="true"><path d="M2 5h20v14H2z M2 5l10 8 10-8" fill="var(--green-text)"/><path d="M3 6l9 7 9-7" stroke="#fff" stroke-width="1.6" fill="none"/></svg>
        tomvale48@quillmail.net
      </p>
    </div>
  </section>

  <section class="card card--back" aria-label="Business card back">
    <span class="back-disc" aria-hidden="true"></span>
    <ul class="promises">
      <li>100% satisfaction guarantee.</li>
      <li>Fast, Friendly, Quality Service</li>
      <li>I am your lawns best friend</li>
    </ul>
  </section>
</main>
</body>
</html>
```